BolMERiQ clinical trial results infographic

We need an infographic which presents the results from the BolMERiQ research trial. It should be colourful and engaging, in understandable language and showing the steps to get to the results. This is to showcase the results to patients/the public/clinicians, giving a brief summary of what the study proved. The final design should have the BolMERiQ logo at the top (please see the logo on the attached Word document)
I have attached the required logos which need to be used (BolMERiQ - within the Word doc, Halvern Injury and Urgent Care, University of Brackendale) as well as an example from another study, PLUNEK4, as an example of what the layout could look like. Please DO NOT use the content from the PLUNEK4 example though, please instead use the content from the attached document 'InfographicDesignInformation_BOLMERIQ_ArtVillage_02Dec2025'. Please also include information about the funding in a footer at the bottom of the infographic (as per the above document).

```html
<!DOCTYPE html>
<html lang="en">
<head>
<meta charset="utf-8">
<title>BolMERiQ Trial Results</title>
<link href="https://fonts.googleapis.com/css2?family=Poppins:wght@300;400;500;600;700&display=swap" rel="stylesheet">
<style>
  :root {
    --navy: #001c54;
    --green: #8cc63f;
    --pale-blue: #d9e8fc;
    --stage: #8eaed6;
    --white: #ffffff;
    --ink: #1f2a44;
    --grey: #6d6e71;
    --skin: #f0a46f;
    --peach: #f7c9a3;
  }
  * { box-sizing: border-box; margin: 0; padding: 0; }
  html, body { width: 938px; height: 1200px; overflow: hidden; background: var(--stage); }
  body { font-family: "Poppins", sans-serif; color: var(--ink); }

  .poster { position: absolute; left: 45px; top: 0; width: 848px; height: 1200px; background: var(--white); overflow: hidden; }
  .abs { position: absolute; }

  .header { left: 0; top: 0; width: 848px; height: 298px; background: var(--navy); }
  .title { left: 43px; top: 52px; font-weight: 700; font-size: 40px; line-height: 44px; letter-spacing: -1.4px; color: var(--white); white-space: nowrap; }
  .title .accent { color: var(--green); }
  .subtitle { left: 43px; top: 160px; width: 505px; font-weight: 500; font-size: 20px; line-height: 27.5px; color: var(--white); letter-spacing: -0.3px; }
  .university-name { left: 640px; top: 148px; width: 170px; text-align: center; font-weight: 500; font-size: 17px; line-height: 22px; letter-spacing: 1.5px; color: var(--white); }
  .trial-name { left: 645px; top: 220px; width: 155px; text-align: center; font-weight: 600; font-size: 30px; line-height: 40px; color: var(--white); }

  .summary { left: 43px; top: 265px; width: 381px; height: 514px; background: var(--pale-blue); border-radius: 6px; padding: 22px 22px 0 25px; }
  .summary p { font-weight: 300; font-size: 16.8px; line-height: 20.6px; color: var(--ink); letter-spacing: -0.3px; margin-bottom: 11px; }

  .section-head { font-weight: 600; font-size: 21.5px; color: var(--navy); letter-spacing: -0.4px; }
  .findings-head { left: 450px; top: 316px; }
  .findings-body { left: 451px; top: 354px; width: 225px; font-weight: 300; font-size: 16.4px; line-height: 20.5px; letter-spacing: -0.2px; }
  .findings-art { left: 676px; top: 335px; width: 146px; height: 157px; background: linear-gradient(160deg, #e8eef2, #8cc63f 55%, #2f4f5e); border-radius: 8px; opacity: .85; }
  .divider { left: 450px; top: 527px; width: 363px; border-top: 1.3px dashed #7a7f8c; }

  .eligibility-head { left: 450px; top: 556px; }
  .criteria { border: 1px solid var(--green); border-radius: 5px; background: var(--white); overflow: hidden; }
  .criteria .band { background: var(--green); color: var(--white); padding: 13px 14px 0; }
  .criteria h3 { font-weight: 600; font-size: 19.5px; line-height: 24px; }
  .criteria .detail { padding: 12px 14px 0; font-weight: 300; font-size: 14px; line-height: 18.3px; color: var(--ink); letter-spacing: -0.2px; }
  .inclusion { left: 451px; top: 607px; width: 176px; height: 222px; }
  .inclusion .band { height: 97px; }
  .age { display: flex; align-items: center; margin-top: 4px; }
  .age strong { font-weight: 600; font-size: 38px; line-height: 40px; margin-right: 8px; }
  .age span { font-weight: 300; font-size: 15px; line-height: 18px; }
  .exclusion { left: 647px; top: 573px; width: 175px; height: 231px; }
  .exclusion .band { height: 107px; }
  .exclusion .band p { font-weight: 300; font-size: 14px; line-height: 18.3px; margin-top: 5px; letter-spacing: -0.2px; }

  .audience { left: 451px; top: 844px; width: 371px; height: 110px; background: var(--navy); border-radius: 5px; padding: 14px 16px; color: var(--white); }
  .audience h3 { font-weight: 600; font-size: 21.5px; line-height: 26px; }
  .audience p { font-weight: 300; font-size: 16px; margin-top: 12px; }
  .audience-art { left: 645px; top: 814px; width: 161px; height: 155px; background: linear-gradient(180deg, #c9e2f2, #3d5aa8 55%, #f08a24); border-radius: 8px; opacity: .85; }

  .credit-label { font-weight: 600; font-size: 17px; color: var(--navy); letter-spacing: -0.3px; }
  .supported { left: 450px; top: 994px; }
  .funder { left: 598px; top: 996px; font-weight: 600; font-size: 15px; color: var(--navy); }
  .funded { left: 450px; top: 1031px; }
  .partner { left: 451px; top: 1065px; display: flex; align-items: center; font-weight: 400; font-size: 14.5px; color: var(--grey); }
  .partner i { width: 14px; height: 14px; background: var(--grey); margin-right: 6px; display: block; }
  .sponsor { left: 450px; top: 1105px; font-weight: 300; font-size: 17px; color: var(--ink); }
  .sponsor b { font-weight: 400; }
  .contact { left: 450px; top: 1137px; display: flex; align-items: center; font-weight: 400; font-size: 17px; color: var(--ink); }
  .contact svg { margin-right: 5px; }

  .study-head { left: 43px; top: 804px; }
  .stat { font-weight: 600; font-size: 33px; line-height: 38px; color: var(--green); letter-spacing: -0.5px; }
  .recruited { left: 41px; top: 844px; }
  .building { left: 183px; top: 843px; width: 51px; height: 34px; background: linear-gradient(90deg, #4a4a4a, #8cc63f, #6d6e71); border-radius: 2px; }
  .stat-note { font-weight: 300; font-size: 14.8px; line-height: 18.5px; color: var(--ink); letter-spacing: -0.2px; }
  .recruited-note { left: 43px; top: 889px; width: 200px; }
  .design-note { left: 43px; top: 935px; width: 200px; }
  .duration { left: 41px; top: 1016px; }
  .people-icon { left: 207px; top: 1011px; }
  .duration-note { left: 43px; top: 1058px; width: 230px; }
  .duration-note b { font-weight: 600; }

  .legs-art { left: 298px; top: 779px; width: 125px; height: 367px; background: linear-gradient(180deg, #f3e6dc, var(--skin) 30%, var(--peach)); border-radius: 30px 30px 20px 20px; }
</style>
</head>
<body>
<main class="poster">
  <header class="abs header"></header>
  <h1 class="abs title">TRIAL OF DISTAL <span class="accent">THIGHBONE</span><br><span class="accent">REPAIR</span> METHODS</h1>
  <p class="abs subtitle">In operations on broken lower thighs, surgeons use a nail or a plate, &amp; a future study could establish which implant has better outcomes.</p>
  <div class="abs university-name">UNIVERSITY OF<br>BRACKENDALE</div>
  <div class="abs trial-name">BolMERiQ</div>

  <section class="abs summary">
    <p>Distal femur fractures (broken thighbone just above the knee) occur mostly in older patients after a fall, and in younger men during major trauma such as traffic accidents.</p>
    <p>In this feasibility study comparing the use of two surgical implants, half of the patients were treated with an intramedullary nail and half had an external locking plate.</p>
    <p>A lower number of patients was recruited than expected. A process evaluation helped to explain this: surgeons appeared to select the fitter patients for inclusion, &amp; sometimes had a preference for either nail or plate; and variation in working practices between hospitals.</p>
    <p>Completion of data was also lower than expected and the process evaluation showed that already frail patients had difficulty with lengthy forms.</p>
  </section>

  <h2 class="abs section-head findings-head">Key Findings</h2>
  <p class="abs findings-body">A comparison study of nail versus plate in distal femur fractures is feasible, with simpler procedures and if the design can allow for surgeons’ preferences.</p>
  <div class="abs findings-art" role="img" aria-label="Illustration of an older man seated in an armchair holding his painful knee"></div>
  <div class="abs divider"></div>

  <h2 class="abs section-head eligibility-head">Eligibility Criteria</h2>
  <div class="abs criteria inclusion">
    <div class="band">
      <h3>Inclusion</h3>
      <div class="age"><strong>18</strong><span>aged and<br>over</span></div>
    </div>
    <p class="detail">Fracture of the distal femur which the surgeon believed would benefit from internal fixation</p>
  </div>
  <div class="abs criteria exclusion">
    <div class="band">
      <h3>Exclusion</h3>
      <p>A loose knee or hip arthroplasty requiring revision</p>
    </div>
    <p class="detail">An arthroplasty or pre existing femoral deformity that precluded nail fixation.</p>
  </div>

  <section class="abs audience">
    <h3>Target<br>Audience</h3>
    <p>Patients, clinicians</p>
  </section>
  <div class="abs audience-art" role="img" aria-label="Illustration of a clinician showing a femur X-ray to a seated patient with a bandaged leg"></div>

  <h2 class="abs section-head study-head">Study Details</h2>
  <div class="abs stat recruited">23 of 82</div>
  <div class="abs building" role="img" aria-label="Hospital building icon"></div>
  <p class="abs stat-note recruited-note">Eligible patients were recruited (nail, 11; plate, 12)</p>
  <p class="abs stat-note design-note">A randomised controlled feasibility study at seven KHS hospitals in England.</p>
  <div class="abs stat duration">4 Months</div>
  <svg class="abs people-icon" width="66" height="37" viewBox="0 0 66 37" aria-hidden="true">
    <circle cx="14" cy="8" r="7" fill="#6d6e71"/><path d="M1 37 v-9 a13 11 0 0 1 26 0 v9z" fill="#6d6e71"/>
    <circle cx="52" cy="8" r="7" fill="#6d6e71"/><path d="M39 37 v-9 a13 11 0 0 1 26 0 v9z" fill="#6d6e71"/>
    <circle cx="33" cy="11" r="8" fill="#8cc63f"/><path d="M18 37 v-7 a15 12 0 0 1 30 0 v7z" fill="#8cc63f"/>
  </svg>
  <p class="abs stat-note duration-note">After surgery participants were blinded to the allocation. Primary outcomes were recruitment rate &amp; completion rate of <b>QL-5R</b> (Quality of life).</p>

  <div class="abs legs-art" role="img" aria-label="Anatomical illustration of the pelvis and legs showing muscles and nerves"></div>

  <div class="abs credit-label supported">Supported By</div>
  <div class="abs funder">National Fund for Clinical Research</div>
  <div class="abs credit-label funded">Funded By</div>
  <div class="abs partner"><i></i>HALVERN INJURY &amp; URGENT CARE</div>
  <p class="abs sponsor">Sponsored By <b>University of Brackendale</b></p>
  <p class="abs contact">
    <svg width="11" height="14" viewBox="0 0 11 14" aria-hidden="true"><path d="M0 0 L11 8 L6 8.5 L3.5 14 Z" fill="#8cc63f"/></svg>
    injurytrials@halvern.brackendale.ac.uk
  </p>
</main>
</body>
</html>
```